Logistics Website Design

See website https://tqfreightglobal.com for theme and color details. Need the site to be re-done and reflect some of the designs shown in this list here: https://pixelvane.com/tags/logistics-company-website

Target Market(s)

Logistics & Transportation

Industry/Entity Type

Logistics and Supply Chain

Coding

Number of Pages Required

5+ page

Requirements
Must have
• Colors must match theme of logo. Looking for a sleek, interactive design.

```html
<!DOCTYPE html>
<html lang="en">
<head>
<meta charset="UTF-8">
<title>TQ Freight Global — Logistics</title>
<link href="https://fonts.googleapis.com/css2?family=Poppins:wght@400;500;600;800&family=Inter:ital,wght@0,400;0,500;0,600;0,700;1,400&display=swap" rel="stylesheet">
<style>
:root{
  --accent:#c98b6e;
  --accent-dark:#b87a5d;
  --ink:#1e2126;
  --ink-soft:#3d4654;
  --muted:#5b6270;
  --mist:#f6f8fa;
  --charcoal:#3f3f3f;
  --night:#1f1f1f;
  --line:#e6d6cc;
  --white:#ffffff;
}
*{box-sizing:border-box;margin:0;padding:0}
html,body{width:1200px;height:3625px;overflow:hidden}
body{font-family:'Inter',sans-serif;color:var(--ink);background:var(--white);position:relative}
.abs{position:absolute}
section,header,footer{position:absolute;left:0;width:1200px}

/* header */
.site-header{top:0;height:75px;background:var(--white);border-bottom:1px solid #eee;z-index:2}
.brand{left:30px;top:22px;display:flex;align-items:center;gap:10px;font-family:'Poppins',sans-serif;font-weight:600;font-size:17px;color:var(--ink)}
.brand-dot{width:28px;height:28px;border-radius:50%;background:var(--accent)}
.nav{left:362px;top:28px;display:flex;gap:30px;font-size:13px;color:#333}
.nav a{color:inherit;text-decoration:none}
.nav .active{color:var(--accent);border-bottom:1px solid var(--accent);padding-bottom:8px}
.btn{display:inline-flex;align-items:center;justify-content:center;background:var(--accent);color:var(--white);border-radius:4px;text-decoration:none}
.header-cta{left:1006px;top:20px;width:163px;height:36px;font-size:15px}

/* hero */
.hero{top:75px;height:722px;background:#1c2430}
.hero-photo{inset:0;background:
  radial-gradient(ellipse 520px 180px at 880px 80px,rgba(245,120,60,.95),rgba(245,120,60,0) 75%),
  radial-gradient(ellipse 420px 140px at 1050px 180px,rgba(230,90,60,.8),rgba(230,90,60,0) 75%),
  radial-gradient(ellipse 380px 260px at 880px 400px,rgba(190,198,210,.75),rgba(190,198,210,0) 70%),
  radial-gradient(ellipse 320px 120px at 620px 560px,rgba(255,190,110,.55),rgba(255,190,110,0) 75%),
  radial-gradient(ellipse 600px 110px at 700px 680px,rgba(255,150,70,.35),rgba(255,150,70,0) 75%),
  radial-gradient(ellipse 420px 420px at 120px 150px,rgba(30,40,45,.9),rgba(30,40,45,0) 70%),
  linear-gradient(180deg,#b8603e 0%,#6e4a52 28%,#3a4456 52%,#262d38 75%,#1a1f28 100%)}
.hero-title{left:31px;top:165px;font-family:'Poppins',sans-serif;font-weight:800;font-size:80px;line-height:72px;color:var(--white);letter-spacing:1px}
.hero-sub{left:31px;top:410px;width:430px;font-size:19px;line-height:27px;color:var(--white)}
.hero-cta{left:31px;top:493px;width:192px;height:48px;font-size:17px}

/* about */
.about{top:797px;height:613px;background:var(--white)}
.about-photo{left:0;top:108px;width:582px;height:380px;background:
  radial-gradient(ellipse 150px 110px at 330px 170px,rgba(180,80,30,.95),rgba(180,80,30,0) 80%),
  radial-gradient(ellipse 110px 120px at 470px 210px,rgba(200,200,205,.9),rgba(200,200,205,0) 80%),
  radial-gradient(ellipse 260px 40px at 320px 330px,rgba(60,60,60,.35),rgba(60,60,60,0) 80%),
  radial-gradient(ellipse 140px 130px at 80px 140px,rgba(215,218,222,.95),rgba(215,218,222,0) 80%),
  linear-gradient(90deg,#f4f4f4,#fafafa)}
.section-title{font-weight:600;font-size:32px;letter-spacing:.5px;color:var(--ink)}
.section-sub{font-weight:600;font-size:22px;letter-spacing:.5px;color:var(--ink-soft)}
.about-title{left:620px;top:110px}
.about-sub{left:620px;top:158px}
.about-text{left:620px;top:210px;width:480px;font-size:15px;line-height:24px;color:var(--muted)}
.about-text strong{font-weight:400;color:var(--ink)}
.about-list{left:620px;top:305px;list-style:none;font-size:15px;color:#333}
.about-list li{display:flex;align-items:center;gap:11px;height:33.5px}
.about-list li::before{content:"";width:7px;height:7px;border-radius:50%;background:var(--accent)}
.about-cta{left:620px;top:432px;width:136px;height:44px;font-size:14px}

/* mission */
.mission{top:1410px;height:800px;background:var(--mist)}
.center-text{left:0;width:1200px;text-align:center}
.mission-title{top:72px}
.mission-sub{top:118px}
.tile{border-radius:3px}
.tile-map{left:90px;top:194px;width:502px;height:180px;background:
  radial-gradient(ellipse 200px 60px at 250px 90px,rgba(230,210,120,.55),rgba(230,210,120,0) 80%),
  radial-gradient(ellipse 120px 90px at 60px 40px,rgba(150,190,215,.5),rgba(150,190,215,0) 80%),
  linear-gradient(180deg,#5a7f9c 0%,#2f4d68 55%,#3f6582 100%)}
.tile-plane{left:607px;top:194px;width:502px;height:180px;background:
  radial-gradient(ellipse 180px 50px at 230px 110px,rgba(40,80,160,.75),rgba(40,80,160,0) 80%),
  radial-gradient(ellipse 90px 40px at 190px 120px,rgba(230,200,60,.55),rgba(230,200,60,0) 80%),
  radial-gradient(ellipse 200px 40px at 420px 95px,rgba(255,110,40,.6),rgba(255,110,40,0) 80%),
  linear-gradient(180deg,#e6b58c 0%,#d99a6e 45%,#8a8580 70%,#4c5260 100%)}
.tile-truck{left:90px;top:389px;width:244px;height:180px;background:
  radial-gradient(ellipse 55px 60px at 100px 85px,rgba(40,90,180,.9),rgba(40,90,180,0) 85%),
  radial-gradient(ellipse 55px 55px at 150px 95px,rgba(235,200,50,.85),rgba(235,200,50,0) 85%),
  radial-gradient(ellipse 110px 20px at 120px 150px,rgba(40,40,40,.35),rgba(40,40,40,0) 85%),
  linear-gradient(180deg,#ececec,#d6d6d6)}
.tile-rail{left:349px;top:389px;width:502px;height:180px;background:
  radial-gradient(ellipse 120px 50px at 380px 110px,rgba(205,170,60,.55),rgba(205,170,60,0) 80%),
  radial-gradient(ellipse 160px 70px at 140px 100px,rgba(70,85,110,.7),rgba(70,85,110,0) 80%),
  linear-gradient(180deg,#e0b08a 0%,#9a8d8f 35%,#4f5c70 60%,#3a4250 100%)}
.tile-van{left:866px;top:389px;width:243px;height:180px;background:
  radial-gradient(ellipse 90px 55px at 125px 85px,rgba(252,252,252,1),rgba(252,252,252,0) 85%),
  radial-gradient(ellipse 100px 18px at 125px 140px,rgba(40,40,40,.3),rgba(40,40,40,0) 85%),
  linear-gradient(180deg,#c9ccce,#b7babd)}
.mission-rule{left:180px;width:840px;height:1px;background:var(--line)}
.mission-text{left:200px;top:646px;width:800px;text-align:center;font-style:italic;font-size:14px;line-height:24px;color:var(--ink-soft)}

/* quote */
.quote{top:2210px;height:357px;background:var(--charcoal);color:var(--white)}
.quote-title{left:90px;top:62px;font-weight:600;font-size:22px;letter-spacing:.5px}
.field{width:235px;height:35px;border:1px solid #8a8a8a;border-radius:2px;font-size:12px;color:#b5b5b5;padding:0 15px;display:flex;align-items:center}
.submit{left:90px;top:263px;width:243px;height:34px;font-size:12px;letter-spacing:.5px}
.divider{left:622px;top:58px;width:1px;height:242px;background:#5a5a5a}
.contact-title{left:667px;top:82px;font-weight:600;font-size:27px;line-height:35px;letter-spacing:.5px}
.contact-phone{left:667px;top:220px;font-weight:600;font-size:22px;color:var(--accent)}
.contact-note{left:667px;top:256px;font-size:13px;color:#bdbdbd}

/* testimonials */
.testimonials{top:2567px;height:538px;background:var(--white)}
.testi-title{top:88px}
.testi-sub{top:137px;font-size:18px}
.testi-card{left:287px;top:208px;width:626px;height:255px;background:var(--white);border-radius:6px;box-shadow:0 4px 22px rgba(0,0,0,.06)}
.avatar{left:283px;top:36px;width:60px;height:60px;border-radius:50%;background:linear-gradient(160deg,#c9b3a3,#8d6e5c);border:2px solid var(--accent)}
.testi-name{left:0;top:117px;width:626px;text-align:center;font-weight:600;font-size:16px;letter-spacing:.5px}
.testi-role{left:0;top:141px;width:626px;text-align:center;font-weight:600;font-size:10px;letter-spacing:1.5px;color:var(--muted)}
.testi-quote{left:40px;top:176px;width:546px;text-align:center;font-style:italic;font-size:12.5px;line-height:21px;color:var(--ink-soft)}
.arrow{width:28px;height:28px;border-radius:50%;background:#f3e4dc}

/* footer */
.site-footer{top:3105px;height:520px;background:var(--night);color:#cfcfcf}
.video{left:90px;top:61px;width:360px;height:201px;border-radius:3px;background:
  radial-gradient(ellipse 140px 50px at 250px 40px,rgba(230,150,80,.55),rgba(230,150,80,0) 80%),
  radial-gradient(ellipse 120px 40px at 130px 110px,rgba(140,140,140,.45),rgba(140,140,140,0) 80%),
  radial-gradient(ellipse 140px 40px at 240px 165px,rgba(200,170,120,.4),rgba(200,170,120,0) 80%),
  linear-gradient(180deg,#6e5a4a 0%,#52443a 50%,#3a322c 100%)}
.play{left:160px;top:80px;width:42px;height:42px}
.social{top:292px;display:flex;gap:18px;left:90px}
.social span{width:16px;height:16px;border-radius:50%;background:#cfcfcf;display:block}
.foot-head{font-weight:600;font-size:16px;letter-spacing:.5px;color:var(--white)}
.foot-links{list-style:none;font-size:12.5px;line-height:26.3px}
.foot-links .active{color:var(--accent)}
.foot-contact{font-size:12.5px;line-height:16px}
.foot-contact p{margin-bottom:12px}
.foot-rule{left:90px;top:415px;width:1020px;height:1px;background:#3a3a3a}
.copyright{left:0;top:447px;width:1200px;text-align:center;font-size:11px;color:#bdbdbd}
</style>
</head>
<body>

<header class="site-header">
  <div class="abs brand"><span class="brand-dot"></span>TQ Freight Global</div>
  <nav class="abs nav">
    <a class="active" href="#">Home</a><a href="#">Services</a><a href="#">Industries</a><a href="#">Request a Quote</a><a href="#">Contact Us</a>
  </nav>
  <a class="abs btn header-cta" href="#">Request a Quote</a>
</header>

<section class="hero">
  <div class="abs hero-photo" role="img" aria-label="Silver semi truck speeding along a highway at sunset"></div>
  <h1 class="abs hero-title">DELIVERING<br>STRENGTH IN<br>EVERY MILE</h1>
  <p class="abs hero-sub">Secure and reliable transportation for all your cargo needs.</p>
  <a class="abs btn hero-cta" href="#">Request a Quote</a>
</section>

<section class="about">
  <div class="abs about-photo" role="img" aria-label="Orange semi truck with white trailer"></div>
  <h2 class="abs section-title about-title">ABOUT US.</h2>
  <h3 class="abs section-sub about-sub">REDEFINING LOGISTICS EXCELLENCE.</h3>
  <p class="abs about-text"><strong>TQ Freight Global</strong> is your dedicated partner in premium logistics. We deliver beyond boundaries with precision and elegance, backed by cutting-edge technology.</p>
  <ul class="abs about-list">
    <li>Real-Time Cargo Tracking</li>
    <li>Secure &amp; On-Time Deliveries</li>
    <li>Customized High-End Plans</li>
  </ul>
  <a class="abs btn about-cta" href="#">Learn More</a>
</section>

<section class="mission">
  <h2 class="abs section-title center-text mission-title">OUR MISSION.</h2>
  <h3 class="abs section-sub center-text mission-sub">COMMITTED TO YOUR JOURNEY.</h3>
  <div class="abs tile tile-map" role="img" aria-label="Digital world map showing global shipping routes"></div>
  <div class="abs tile tile-plane" role="img" aria-label="Cargo plane being loaded at an airport at sunset"></div>
  <div class="abs tile tile-truck" role="img" aria-label="Blue and yellow truck cab in a studio"></div>
  <div class="abs tile tile-rail" role="img" aria-label="Freight train crossing a bridge in front of a city skyline"></div>
  <div class="abs tile tile-van" role="img" aria-label="White delivery van"></div>
  <div class="abs mission-rule" style="top:614px"></div>
  <p class="abs mission-text">Our mission is to empower businesses with innovative, sustainable, and dependable logistics solutions. We redefine the industry with refined delivery practices and precision care.</p>
  <div class="abs mission-rule" style="top:723px"></div>
</section>

<section class="quote">
  <h2 class="abs quote-title">REQUEST A QUOTE</h2>
  <div class="abs field" style="left:90px;top:111px">Air Freight</div>
  <div class="abs field" style="left:341px;top:111px">Ocean Freight</div>
  <div class="abs field" style="left:90px;top:162px">Name</div>
  <div class="abs field" style="left:341px;top:162px">Email</div>
  <div class="abs field" style="left:90px;top:213px">Phone</div>
  <div class="abs field" style="left:341px;top:213px">Destination</div>
  <a class="abs btn submit" href="#">SUBMIT</a>
  <div class="abs divider"></div>
  <h2 class="abs contact-title">CONTACT US.<br>YOUR LOGISTICS<br>PARTNER AWAITS.</h2>
  <p class="abs contact-phone">+1 415-555-0142</p>
  <p class="abs contact-note">Have Any Questions?</p>
</section>

<section class="testimonials">
  <h2 class="abs section-title center-text testi-title">TESTIMONIALS.</h2>
  <h3 class="abs section-sub center-text testi-sub">HEAR WHAT OUR PREMIUM CLIENTS HAVE TO SAY</h3>
  <svg class="abs arrow" style="left:241px;top:322px" viewBox="0 0 28 28"><path d="M16 9l-5 5 5 5" fill="none" stroke="#c98b6e" stroke-width="1.5"/></svg>
  <div class="abs testi-card">
    <div class="abs avatar" role="img" aria-label="Client portrait"></div>
    <p class="abs testi-name">MAREN CASTELL</p>
    <p class="abs testi-role">CEO, DOVECREST TRADING</p>
    <p class="abs testi-quote">"TQ Freight Global has transformed our supply chain. Their attention to detail and premium service are unmatched. A truly elegant and reliable partner."</p>
  </div>
  <svg class="abs arrow" style="left:930px;top:322px" viewBox="0 0 28 28"><path d="M12 9l5 5-5 5" fill="none" stroke="#c98b6e" stroke-width="1.5"/></svg>
</section>

<footer class="site-footer">
  <div class="abs video" role="img" aria-label="Aerial view of a truck yard at dusk">
    <svg class="abs play" viewBox="0 0 42 42"><circle cx="21" cy="21" r="21" fill="rgba(0,0,0,.35)"/><path d="M17 14l11 7-11 7z" fill="#fff"/></svg>
  </div>
  <div class="abs social" aria-label="Social links"><span></span><span></span><span></span></div>
  <h4 class="abs foot-head" style="left:619px;top:66px">PAGES</h4>
  <ul class="abs foot-links" style="left:619px;top:98px">
    <li class="active">Home</li><li>About</li><li>Services</li><li>Reviews</li><li>Contact</li>
  </ul>
  <h4 class="abs foot-head" style="left:883px;top:66px">CONTACT</h4>
  <div class="abs foot-contact" style="left:883px;top:102px">
    <p>Address: TQ Freight Global<br>820 Harbor Lane, Oakport 94607</p>
    <p>Email: hello@tqfreightglobal.com</p>
    <p>Phone: +1 415-555-0142</p>
    <p>Work Hours: 9am - 6pm</p>
  </div>
  <div class="abs foot-rule"></div>
  <p class="abs copyright">Copyright © TQ Freight Global 2024</p>
</footer>

</body>
</html>
```